I need 2 flyers designed for my business

Both can be similar in design and will have different purposes. I need an education based flyer and I need a government based flyer. The focus of the flyer will be software on the front and services on the back.
These all need to be 8.5x 11 in dimension (they can be full bleed). I would like to be able to print these out if needed. The design needs to look good with our website > www.brelmont.com

The software details are on the website.

```html
<!DOCTYPE html>
<html lang="en">
<head>
<meta charset="UTF-8">
<title>Services</title>
<link href="https://fonts.googleapis.com/css2?family=Poppins:wght@400;500;600&display=swap" rel="stylesheet">
<style>
:root{
  --navy:#0b3d6e;
  --navy-deep:#1a3d63;
  --navy-light:#3b5f86;
  --cyan:#14a3dc;
  --band:#0ea7e0;
  --body:#5a5a5a;
  --brand-red:#8c1a1e;
  --white:#ffffff;
}
*{margin:0;padding:0;box-sizing:border-box}
html,body{width:927px;height:1200px;overflow:hidden;background:var(--white)}
body{font-family:"Poppins",sans-serif;position:relative}
.hero{position:absolute;left:0;top:0;width:927px;height:520px}
.hero-title{position:absolute;left:0;width:956px;top:228px;text-align:center;color:var(--white);font-weight:600;font-size:56px;letter-spacing:0.5px}
.brand{position:absolute;left:26px;top:466px;display:flex;align-items:center;gap:10px}
.brand-mark{width:26px;height:26px;background:var(--brand-red)}
.brand-name{font-weight:600;font-size:26px;color:var(--brand-red);letter-spacing:-0.3px}
.service{position:absolute;left:0;width:927px;height:200px}
.service-icon{position:absolute;left:116px;top:0;width:80px;height:76px}
.service-name{position:absolute;left:0;width:312px;top:84px;text-align:center;color:var(--navy);font-weight:500;font-size:23px;line-height:27px}
.service-col{position:absolute;top:0;color:var(--navy);font-weight:500;font-size:15.5px;line-height:18px}
.service-col.about{left:354px;width:260px}
.service-col.formats{left:647px;width:280px}
.service-desc{margin-top:40px;color:var(--body);font-weight:400;font-size:13.6px;line-height:16.4px;width:262px}
.format-list{list-style:none;margin-top:36px;color:var(--body);font-weight:400;font-size:13.6px;line-height:16.4px}
.format-list li::before{content:"• "}
.footer{position:absolute;left:0;top:1155px;width:927px;height:45px;background:var(--band);color:var(--white);font-size:15px;display:flex;align-items:center;justify-content:center}
</style>
</head>
<body>
<svg class="hero" viewBox="0 0 927 520" role="img" aria-label="Office photo of colleagues working together at computers">
  <defs>
    <linearGradient id="heroTone" x1="0" y1="0" x2="1" y2="1">
      <stop offset="0" stop-color="#4a6a8e"/>
      <stop offset="0.5" stop-color="#2f5278"/>
      <stop offset="1" stop-color="#1a3d63"/>
    </linearGradient>
  </defs>
  <polygon points="0,0 927,0 927,96 733,209 733,373 473,519 0,247" fill="url(#heroTone)"/>
</svg>
<h1 class="hero-title">Services</h1>

<div class="brand">
  <span class="brand-mark"></span>
  <span class="brand-name">Keystone Records</span>
</div>

<section class="service" style="top:593px">
  <svg class="service-icon" viewBox="0 0 80 76" fill="none" stroke="var(--cyan)" stroke-width="3">
    <polygon points="40,2 77,22 40,42 3,22"/>
    <polyline points="12,31 3,37 40,57 77,37 68,31"/>
    <polyline points="12,46 3,52 40,73 77,52 68,46"/>
  </svg>
  <h2 class="service-name">Document Scanning<br>Services</h2>
  <div class="service-col about">Document Scanning<br>Services
    <p class="service-desc">Fast, efficient process for the conversion of existing paper records to digital archives, increasing access and reducing onsite storage and costs.</p>
  </div>
  <div class="service-col formats">Scanning services for<br>any format:
    <ul class="format-list"><li>Standard Office Documents</li><li>16mm, 35mm Roll Microfilm</li><li>Microfiche (Jackets or COM)</li><li>Large Format Documents/Drawings</li></ul>
  </div>
</section>

<section class="service" style="top:793px">
  <svg class="service-icon" viewBox="0 0 80 76" fill="none" stroke="var(--cyan)" stroke-width="3">
    <path d="M12,30 V17 a15,15 0 0 1 30,0 V23"/>
    <rect x="10" y="30" width="56" height="44"/>
    <line x1="10" y1="66" x2="66" y2="66"/>
    <ellipse cx="38" cy="49" rx="4" ry="7"/>
  </svg>
  <h2 class="service-name">Document Storage<br>Services</h2>
  <div class="service-col about">Document Scanning<br>Services
    <p class="service-desc">Fast, efficient process for the conversion of existing paper records to digital archives, increasing access and reducing onsite storage and costs.</p>
  </div>
  <div class="service-col formats">Scanning services for<br>any format:
    <ul class="format-list"><li>Standard Office Documents</li><li>16mm, 35mm Roll Microfilm</li><li>Microfiche (Jackets or COM)</li><li>Large Format Documents/Drawings</li></ul>
  </div>
</section>

<section class="service" style="top:996px">
  <svg class="service-icon" viewBox="0 0 80 76" fill="none" stroke="var(--cyan)" stroke-width="3">
    <polygon points="7,2 73,2 77,8 77,18 3,18 3,8"/>
    <rect x="8" y="18" width="64" height="56"/>
    <rect x="25" y="30" width="30" height="10"/>
    <rect x="18" y="48" width="44" height="14"/>
    <line x1="24" y1="55" x2="56" y2="55" stroke-dasharray="4 3"/>
  </svg>
  <h2 class="service-name">Secure Document<br>Shredding</h2>
  <div class="service-col about">Document Scanning<br>Services
    <p class="service-desc">Fast, efficient process for the conversion of existing paper records to digital archives, increasing access and reducing onsite storage and costs.</p>
  </div>
  <div class="service-col formats">Scanning services for<br>any format:
    <ul class="format-list"><li>Standard Office Documents</li><li>16mm, 35mm Roll Microfilm</li><li>Microfiche (Jackets or COM)</li><li>Large Format Documents/Drawings</li></ul>
  </div>
</section>

<footer class="footer">Sales inquiries to (555) 318-4702 or help@keystonerecords.org</footer>
</body>
</html>
```